I need a label design to go on our jars of honey. Our company is called Marrowdale Honey Co. The type of honey is called Fernlight Glen Honey. The jars are 1kg. Attached is the label size. Left hand side needs to have nutritional info... as attached. Middle section is our company name, honey type, 1kg & Whangamata, NZ. Right hand side needs to have info as per photo (raw honey etc). I would like to upload more pictures... but I’m unsure how to do this? Thanks, Carla

Target Market(s)

Honey consumers... families

Industry/Entity Type

Food Production

Colors

Designer to choose colors to be used in the design.

Requirements
Must have
• Nutritional info as per upload
• Type of honey & company name as per upload
• 1kg
• Address
Nice to have
• Similar fonts to upload.
• Possibly background image... floral or beach... very faint though.

```html
<!DOCTYPE html>
<html lang="en">
<head>
<meta charset="utf-8">
<title>Marrowdale Honey Co. – Fernlight Glen Honey label</title>
<link rel="stylesheet" href="https://fonts.googleapis.com/css2?family=Amatic+SC:wght@700&family=Arimo:ital,wght@0,400;1,400&family=Caveat+Brush&family=Raleway:wght@300&display=swap">
<style>
  :root {
    --label-olive: #8b7b22;
    --label-olive-deep: #7a6c1b;
    --bloom-core: #e0a024;
    --bloom-mid: #d08a1e;
    --bloom-edge: rgba(160, 130, 30, 0);
    --ink-light: #fbf6e6;
    --ink-dark: #1d1a10;
    --panel-white: #ffffff;
  }
  * { box-sizing: border-box; margin: 0; padding: 0; }
  html, body { width: 1200px; height: 477px; overflow: hidden; background: var(--label-olive); }
  .label {
    position: relative;
    width: 1200px;
    height: 477px;
    background: radial-gradient(ellipse at 50% 50%, var(--label-olive) 0%, var(--label-olive-deep) 100%);
    color: var(--ink-light);
    font-family: "Arimo", Arial, sans-serif;
  }
  .flower-backdrop {
    position: absolute;
    left: 378px; top: 18px;
    width: 440px; height: 440px;
    border-radius: 50%;
    background: radial-gradient(circle, var(--bloom-core) 0%, var(--bloom-mid) 45%, var(--bloom-edge) 72%);
  }

  /* Left: nutrition */
  .claim {
    position: absolute; left: 63px; width: 264px; top: 26px;
    text-align: center; font-style: italic; font-size: 13.5px; line-height: 17px;
  }
  .nutrition {
    position: absolute; left: 63px; top: 63px; width: 264px; height: 261px;
    border: 1px solid var(--ink-light);
    font-size: 9px;
  }
  .nutrition-head {
    height: 48px; padding: 8px 5px; line-height: 11px;
    border-bottom: 1px solid var(--ink-light);
  }
  .nutrition-table { width: 100%; border-collapse: collapse; }
  .nutrition-table th, .nutrition-table td {
    text-align: left; font-weight: 400; padding: 0 5px;
  }
  .nutrition-table thead th {
    height: 34px; border-bottom: 1px solid var(--ink-light); line-height: 11px;
  }
  .nutrition-table th + th, .nutrition-table td + td { border-left: 1px solid var(--ink-light); }
  .nutrition-table tbody td { height: 25px; font-size: 9.5px; }
  .nutrition-table tbody tr:first-child td { padding-top: 4px; }
  .storage {
    position: absolute; left: 30px; width: 330px; top: 338px;
    text-align: center; font-style: italic; font-size: 11.5px; line-height: 17px;
  }
  .batch-box {
    position: absolute; left: 66px; top: 381px; width: 271px; height: 74px;
    background: var(--panel-white); color: var(--ink-dark);
    padding: 8px 7px; font-style: italic; font-size: 11px; line-height: 14px;
  }

  /* Middle: brand */
  .brand-name {
    position: absolute; left: 378px; width: 440px; top: 62px; text-align: center;
    font-family: "Amatic SC", "Arial Narrow", sans-serif; font-weight: 700;
    font-size: 27px; letter-spacing: 9px;
  }
  .honey-kind {
    position: absolute; left: 378px; width: 440px; top: 186px; text-align: center;
    font-family: "Raleway", Arial, sans-serif; font-weight: 300;
    font-size: 26px; letter-spacing: 12px;
  }
  .honey-name {
    position: absolute; left: 330px; width: 536px; top: 220px; text-align: center;
    font-family: "Caveat Brush", cursive; font-size: 66px; line-height: 80px;
  }
  .weight {
    position: absolute; left: 378px; width: 440px; top: 355px; text-align: center;
    font-family: "Amatic SC", "Arial Narrow", sans-serif; font-weight: 700; font-size: 24px;
  }
  .weight-rule {
    position: absolute; left: 583px; top: 399px; width: 30px; height: 2px; background: var(--ink-light);
  }
  .origin {
    position: absolute; left: 378px; width: 440px; top: 422px; text-align: center;
    font-family: "Amatic SC", "Arial Narrow", sans-serif; font-weight: 700;
    font-size: 25px; letter-spacing: 4px;
  }

  /* Right: story & contact */
  .story, .contact {
    position: absolute; left: 887px; width: 260px; text-align: center;
    font-size: 14.5px; line-height: 21px;
  }
  .story { top: 40px; }
  .story p + p { margin-top: 17px; }
  .contact-rule {
    position: absolute; left: 905px; top: 330px; width: 216px; height: 2px; background: var(--ink-light);
  }
  .contact { top: 344px; line-height: 20.5px; }
</style>
</head>
<body>
<main class="label">
  <div class="flower-backdrop" role="img" aria-label="Soft-focus photograph of an orange zinnia flower"></div>

  <section class="panel-left">
    <p class="claim">100% New Zealand Honey<br>No added ingredients</p>
    <div class="nutrition">
      <div class="nutrition-head">NUTRITIONAL INFORMATION<br>Serving per package: 100<br>Serving size: 10g</div>
      <table class="nutrition-table">
        <thead>
          <tr><th style="width:40%"></th><th>Average Quantity<br>per Serving</th><th>Average Quantity<br>per 100g</th></tr>
        </thead>
        <tbody>
          <tr><td>Energy</td><td>134kj</td><td>1340kj</td></tr>
          <tr><td>Protein</td><td>0.04g</td><td>0.4g</td></tr>
          <tr><td>Fat Total</td><td>0g</td><td>0g</td></tr>
          <tr><td>- saturated</td><td>0g</td><td>0g</td></tr>
          <tr><td>Carbohydrate</td><td>7.9g</td><td>79.6g</td></tr>
          <tr><td>- sugars</td><td>7.8g</td><td>78.1g</td></tr>
          <tr><td>Sodium</td><td>1.2mg</td><td>12mg</td></tr>
        </tbody>
      </table>
    </div>
    <p class="storage">Store upright in a cool, dry place. No refrigeration needed.<br>Not recommended for infants below the age of 12 months.</p>
    <div class="batch-box">Best before:<br>RMP:<br>Batch No:</div>
  </section>

  <section class="panel-centre">
    <h1 class="brand-name">MARROWDALE HONEY CO.</h1>
    <p class="honey-kind">FERNLIGHT</p>
    <p class="honey-name">Glen Honey</p>
    <p class="weight">1KG</p>
    <div class="weight-rule"></div>
    <p class="origin">WHANGAMATA, N.Z.</p>
  </section>

  <section class="panel-right">
    <div class="story">
      <p>Sourced from the beautiful<br>Coromandel Peninsula.</p>
      <p>Our honey comes to you raw &amp;<br>unpasteurised, ensuring it retains all<br>natural goodness!</p>
      <p>Arohanui,<br>Tomas, Carla &amp; boys</p>
      <p>‘Marrowdale’ all thanks to God for His<br>incredible creation!</p>
    </div>
    <div class="contact-rule"></div>
    <address class="contact" style="font-style:normal">www.marrowdalehoney.co.nz<br>48 Kereru Lane<br>Whangamata, New Zealand</address>
  </section>
</main>
</body>
</html>
```